Baby Organic Coconut Body Lotion

Meadow Hush Naturals is developing a line of Organic and Natural skin care products for babies and toddlers, although our skin care can also be used by adults too. These products include a body lotion, shampoo & body wash, powder, hair cream, massage body oil, bath soak, baby balm, Bar Soap, gift box and many more.
This will be an ever expanding line so the list will go on and on. We are looking forward for an eye catching designs. I attached some of our current label designs and product images. Also, we have different Baby organic body lotion and Baby organic shampoo & body wash with different fruit flavours. Coconut lotion will share the same design with the shampoo & body wash. I would like you to start with the coconut design. I have uploaded plastic bottles with different colourful caps. The bottle with the white cap is for the coconut design. the bottle with the red cap is for the strawberry design. the bottle with the orange cap is for the orange design. the bottle with the yellow cap is for the pineapple design. the bottle with the green cap is for the apple design. Bear in my mind that my baby organic skin care are made with different fruit flavours.
Target Market(s)
My target market are for mothers that wants to buy there baby and toddler skin care products.
Industry/Entity Type
Baby
Look and feel

```html
<!DOCTYPE html>
<html lang="en">
<head>
<meta charset="utf-8">
<title>Meadow Hush Naturals – Baby Organic Lotion Labels</title>
<link href="https://fonts.googleapis.com/css2?family=Dosis:wght@500;600&display=swap" rel="stylesheet">
<style>
  :root {
    --backdrop: #e7e6e4;
    --label-bg: #f7f7f5;
    --apple: #a3bf55;
    --apple-band: #9cba4f;
    --apple-photo-a: #c9e08a;
    --apple-photo-b: #78a83a;
    --pineapple: #c6b457;
    --pineapple-band: #b7a646;
    --pineapple-photo-a: #f2e14a;
    --pineapple-photo-b: #9c8a3a;
    --strawberry: #c45a62;
    --strawberry-band: #a9333b;
    --strawberry-photo-a: #e0434e;
    --strawberry-photo-b: #b11f2c;
    --orange: #efb622;
    --orange-band: #eda81c;
    --orange-photo-a: #ffc83a;
    --orange-photo-b: #f19a10;
    --coconut: #7b7575;
    --coconut-band: #8a8484;
    --coconut-photo-a: #eeeae4;
    --coconut-photo-b: #7a5a3e;
  }
  * { box-sizing: border-box; margin: 0; padding: 0; }
  html, body { width: 1200px; height: 1200px; overflow: hidden; }
  body {
    background: var(--backdrop);
    font-family: "Dosis", sans-serif;
  }
  .label-row {
    position: absolute;
    left: 28px;
    top: 395px;
    display: flex;
    gap: 16px;
  }
  .label {
    width: 216px;
    height: 410px;
    background: var(--label-bg);
    display: flex;
    flex-direction: column;
    align-items: center;
    box-shadow: 0 2px 6px rgba(0,0,0,0.08);
    color: var(--tone);
  }
  .label--apple { --tone: var(--apple); --band: var(--apple-band); --pa: var(--apple-photo-a); --pb: var(--apple-photo-b); }
  .label--pineapple { --tone: var(--pineapple); --band: var(--pineapple-band); --pa: var(--pineapple-photo-a); --pb: var(--pineapple-photo-b); }
  .label--strawberry { --tone: var(--strawberry); --band: var(--strawberry-band); --pa: var(--strawberry-photo-a); --pb: var(--strawberry-photo-b); }
  .label--orange { --tone: var(--orange); --band: var(--orange-band); --pa: var(--orange-photo-a); --pb: var(--orange-photo-b); }
  .label--coconut { --tone: var(--coconut); --band: var(--coconut-band); --pa: var(--coconut-photo-a); --pb: var(--coconut-photo-b); }

  .brand-name {
    margin-top: 22px;
    height: 78px;
    display: flex;
    align-items: center;
    text-align: center;
    font-size: 26px;
    font-weight: 600;
    line-height: 1.05;
    color: var(--tone);
  }
  .product-name {
    margin-top: 10px;
    height: 88px;
    text-align: center;
    font-size: 28px;
    font-weight: 500;
    line-height: 1.4;
  }
  .label--strawberry .product-name { font-size: 22px; line-height: 1.55; padding-top: 6px; }
  .benefit-band {
    width: 100%;
    height: 34px;
    background: var(--band);
    color: #fff;
    font-size: 15px;
    font-weight: 500;
    display: flex;
    align-items: center;
    justify-content: center;
  }
  .test-note {
    margin-top: 6px;
    font-size: 9px;
    font-weight: 500;
  }
  .fruit-photo {
    position: relative;
    margin-top: auto;
    width: 100%;
    height: 160px;
    background: linear-gradient(135deg, var(--pa), var(--pb));
  }
  .label--coconut .fruit-photo {
    background: linear-gradient(90deg, var(--pa) 0%, var(--pa) 35%, var(--pb) 60%, #5c4330 100%);
  }
  .photo-caption {
    position: absolute;
    left: 0; right: 0; bottom: 0;
    height: 40px;
    padding: 0 18px;
    display: flex;
    align-items: center;
    justify-content: space-between;
    color: #fff;
    font-size: 14px;
    font-weight: 500;
    background: linear-gradient(to top, rgba(255,255,255,0.35), rgba(255,255,255,0));
  }
  .organic-share { font-weight: 600; }
</style>
</head>
<body>
  <main class="label-row">
    <section class="label label--apple">
      <div class="brand-name">Meadow Hush<br>Naturals</div>
      <h2 class="product-name">Baby Organic<br>Apple Lotion</h2>
      <div class="benefit-band">With Shea &amp; Cocoa Butter</div>
      <p class="test-note">Dermatologically tested</p>
      <div class="fruit-photo" role="img" aria-label="Photo of green apples, one cut in half">
        <div class="photo-caption"><span class="organic-share">80% organic</span><span>125ml e</span></div>
      </div>
    </section>

    <section class="label label--pineapple">
      <div class="brand-name">Meadow Hush<br>Naturals</div>
      <h2 class="product-name">Baby Organic<br>Pineapple Lotion</h2>
      <div class="benefit-band">With Shea &amp; Cocoa Butter</div>
      <p class="test-note">Dermatologically tested</p>
      <div class="fruit-photo" role="img" aria-label="Photo of a pineapple with slices">
        <div class="photo-caption"><span class="organic-share">80% organic</span><span>125ml e</span></div>
      </div>
    </section>

    <section class="label label--strawberry">
      <div class="brand-name">Meadow Hush<br>Naturals</div>
      <h2 class="product-name">Baby Organic<br>Strawberry Lotion</h2>
      <div class="benefit-band">With Shea &amp; Cocoa Butter</div>
      <p class="test-note">Dermatologically tested</p>
      <div class="fruit-photo" role="img" aria-label="Photo of ripe red strawberries">
        <div class="photo-caption"><span class="organic-share">80% organic</span><span>125ml e</span></div>
      </div>
    </section>

    <section class="label label--orange">
      <div class="brand-name">Meadow Hush<br>Naturals</div>
      <h2 class="product-name">Baby Organic<br>Orange Lotion</h2>
      <div class="benefit-band">With Shea &amp; Cocoa Butter</div>
      <p class="test-note">Dermatologically tested</p>
      <div class="fruit-photo" role="img" aria-label="Photo of oranges, one cut in half, with a leaf">
        <div class="photo-caption"><span class="organic-share">80% organic</span><span>125ml e</span></div>
      </div>
    </section>

    <section class="label label--coconut">
      <div class="brand-name">Meadow Hush<br>Naturals</div>
      <h2 class="product-name">Baby Organic<br>Apple Lotion</h2>
      <div class="benefit-band">With Shea &amp; Cocoa Butter</div>
      <p class="test-note">Dermatologically tested</p>
      <div class="fruit-photo" role="img" aria-label="Photo of a whole coconut and a cracked coconut half">
        <div class="photo-caption"><span class="organic-share">80% organic</span><span>125ml e</span></div>
      </div>
    </section>
  </main>
</body>
</html>
```